Interior Plaster, Plasterboard Fixing & Installation Business CardDesign

BRANVO The name was formed by me, in talking to my accountant, whilst skim coating his walls and I had seen an imperfection in a wall that needed to be skim coated to deflect the light from the imperfection. I responded to him saying...."just Bran Vo". The idea originates from the process of applying a skim coat of interior plaster to a wall to achieve a smoother surface. This is required prior to many applications, applying wall paper, preparation for paint, after removing wall paper, improving aesthetics, joints that have not been properly jointed etc. Different types of light reflected on the surface, makes poor jointing more visible. In addition, the businesses key functions will be interior plastering, plaster board installation (ceilings and walls) and plasterboard jointing to a level that is prepared for a painter. Once the plaster is applied the surface requires sanding using different types of sanding equipment manual and electronic, including the use of specialised paint-on sealers for the surface. I believe the name is simple, easy to remember, but may be read incorrectly. I have had people ask if it was Bran Vo, referring to information technology.

For now, this entire concept is driven by passion and started 2 years ago whilst renovating my own home.

I need to be able to use your expertise to translate my ideas, starting with business card and progressing to a website incorporating anything and everything in between. The final design should be easy to understand, read and standout with an element of uniqueness. Humour maybe an option, or the idea of leaving a prospect with something that is thought provoking.
Updates

Hi All Ideas look fine so far, but would expect to see different colour options. I am thinking plaster thats cream in colour, so more earthy colour on the card. A picture of a trowel to replace the I in BRANVO maybe. I like the swirl that is created by a notched trowel moving through plaster. Perhaps a more modern or fresher look. With BRANVO, could you consider reversing the direction of the K for instance facing in the opposite direction. In saying this I look to you for your experience and expertise with the idea. The other option with the K, could be to remove the first straight line, i hope that my explanation helps. Sorry if it doesn't. Thanks heaps :)

Please include the type of service. Plasterboard Services

I have considered the idea of the K being reversed, and I am of the view that it presents a challenge reading and understanding. Moving forward I would however like to use the K in the normal direction but without the first straight line. I need to see more colour options that are grey or earthy. Can a picture of a trowel be included if it makes sense and with that tool being frequently used in plastering.

Industry/Entity Type

Business

Contact Information for Business Card

Company name: BranVo
Name: Dorian Pekke
Title: Director
Email address: pekkedp@mailvora.example
Mobile number: 0210 481 7092
Address: 17 Tamsin Lane, Glenfield, Auckland, 0629

```html
<!DOCTYPE html>
<html lang="en">
<head>
<meta charset="utf-8">
<title>BRANVO Business Card</title>
<link rel="stylesheet" href="https://fonts.googleapis.com/css2?family=Cinzel:wght@500;700&display=swap">
<style>
  :root {
    --stage: #e8e6e2;
    --card: #fdfbf6;
    --brand-brown: #6b4a32;
    --deep-earth: #5a3f2b;
    --sand: #c9a675;
    --swoosh-grey: #8d8a85;
    --ink: #3d3a36;
    --divider: #a29d96;
  }
  html, body {
    margin: 0;
    width: 1200px;
    height: 901px;
    overflow: hidden;
    background: var(--stage);
  }
  .card {
    position: absolute;
    left: 100px;
    top: 165px;
    width: 1000px;
    height: 571px;
    background: var(--card);
    border-radius: 56px;
    overflow: hidden;
    box-shadow: 0 10px 30px rgba(0,0,0,0.15);
    font-family: "Cinzel", serif;
    color: var(--ink);
  }
  .card-waves {
    position: absolute;
    inset: 0;
  }
  .brand-name {
    position: absolute;
    top: 70px;
    left: 0;
    width: 100%;
    text-align: center;
    font-size: 76px;
    font-weight: 700;
    letter-spacing: 3px;
    line-height: 1;
    color: var(--brand-brown);
    margin: 0;
  }
  .service-line {
    position: absolute;
    top: 162px;
    left: 0;
    width: 100%;
    text-align: center;
    font-size: 20px;
    font-weight: 500;
    letter-spacing: 5px;
    color: var(--ink);
    margin: 0;
  }
  .identity {
    position: absolute;
    top: 250px;
    right: 530px;
    text-align: right;
    font-size: 19px;
    line-height: 27px;
    letter-spacing: 1.5px;
  }
  .identity .person {
    color: var(--brand-brown);
    font-weight: 700;
    font-size: 21px;
  }
  .identity .role {
    margin-bottom: 10px;
  }
  .divider {
    position: absolute;
    left: 488px;
    top: 252px;
    width: 1px;
    height: 150px;
    background: var(--divider);
  }
  .contacts {
    position: absolute;
    top: 290px;
    left: 508px;
    margin: 0;
    padding: 0;
    list-style: none;
    font-size: 19px;
    letter-spacing: 1.5px;
  }
  .contacts li {
    display: flex;
    align-items: center;
    gap: 10px;
    height: 34px;
  }
  .contact-icon {
    width: 18px;
    height: 18px;
    flex: none;
  }
</style>
</head>
<body>
  <div class="card">
    <svg class="card-waves" width="1000" height="571" viewBox="0 0 1000 571" aria-hidden="true">
      <defs>
        <linearGradient id="bandFill" x1="0" y1="0" x2="1" y2="0">
          <stop offset="0" stop-color="#5a3f2b"/>
          <stop offset="0.5" stop-color="#c9a675"/>
          <stop offset="1" stop-color="#5a3f2b"/>
        </linearGradient>
        <linearGradient id="swooshFill" x1="0" y1="0" x2="1" y2="0">
          <stop offset="0" stop-color="#5e5b57"/>
          <stop offset="0.5" stop-color="#8d8a85"/>
          <stop offset="1" stop-color="#cbc7c1"/>
        </linearGradient>
      </defs>
      <path class="earth-band" d="M0,372 C220,492 560,520 1000,530 L1000,571 L0,571 Z" fill="url(#bandFill)"/>
      <path class="grey-swoosh" d="M0,340 C220,470 560,500 1000,512 L1000,518 C560,508 220,484 0,356 Z" fill="url(#swooshFill)"/>
    </svg>

    <h1 class="brand-name">BRANVO</h1>
    <p class="service-line">Plasterboard Services</p>

    <div class="identity">
      <div class="person">Dorian Pekke</div>
      <div class="role">Director</div>
      <div>17 Tamsin Lane,</div>
      <div>Glenfield, Auckland,</div>
      <div>0629</div>
    </div>

    <div class="divider"></div>

    <ul class="contacts">
      <li>
        <svg class="contact-icon" viewBox="0 0 18 18"><circle cx="9" cy="9" r="9" fill="var(--brand-brown)"/><rect x="6" y="3.5" width="6" height="11" rx="1" fill="#fff"/><rect x="7" y="5" width="4" height="6" fill="var(--brand-brown)"/></svg>
        <span>0210 481 7092</span>
      </li>
      <li>
        <svg class="contact-icon" viewBox="0 0 18 18"><circle cx="9" cy="9" r="9" fill="var(--brand-brown)"/><rect x="4" y="5.5" width="10" height="7" fill="#fff"/><path d="M4 5.5l5 4 5-4" fill="none" stroke="var(--brand-brown)" stroke-width="1"/></svg>
        <span>pekkedp@mailvora.example</span>
      </li>
    </ul>
  </div>
</body>
</html>
```